FinTech company looking to revamp and expand client-facing interface for our financial models

Pellworth Engines currently has a very simple website that allows clients to interact with our financial models. We are looking to completely redesign the current site and add several extra pages to provide extra functionality. We want the design to have a modern, slick feel, that will work on both a desktop or a tablet. It should be straightforward for clients to move between different pages at any time, and clear from the layout how to interact with the more advanced features. We have included screenshots of existing pages in the attached design brief, as well as sketches of the functionality required by the new pages, but can't provide a direct link to the current site.
Target Market(s)
Professional investors that will be paying to access the interface
Industry/Entity Type
Finance
Number of Pages Required
4 page
Colors
Designer to choose colors to be used in the design.
Look and feel
Each slider illustrates characteristics of the customer's brand and the style your logo design should communicate.

```html
<!DOCTYPE html>
<html lang="en">
<head>
<meta charset="utf-8">
<title>Pellworth Engines – Model Interface</title>
<link href="https://fonts.googleapis.com/css2?family=Source+Serif+4:wght@400;600;700&display=swap" rel="stylesheet">
<style>
  :root {
    --page-bg: #303a4e;
    --panel-bg: #eef1f5;
    --header-bg: #ffffff;
    --tab-active: #f0f2f5;
    --ink: #2f3a4f;
    --ink-soft: #3d4658;
    --accent: #19c0ec;
    --head-cell: #f4f6f6;
    --head-cell-key: #d8eef5;
    --row-bg: #ffffff;
    --rule: #e2e5e8;
  }
  * { box-sizing: border-box; margin: 0; padding: 0; }
  html, body { width: 667px; height: 1200px; overflow: hidden; }
  body {
    background: linear-gradient(180deg, #343e52 0%, #2c3447 100%);
    font-family: "Source Serif 4", Georgia, serif;
    color: var(--ink);
    position: relative;
  }
  .screen {
    position: absolute;
    left: 44px;
    width: 579px;
    background: linear-gradient(160deg, #f2f5f8 0%, #eaeef3 60%, #f1f3f6 100%);
    overflow: hidden;
  }
  .screen-one { top: 35px; height: 399px; }
  .screen-two { top: 456px; height: 281px; }
  .screen-three { top: 762px; height: 400px; }

  .topbar {
    position: absolute; left: 0; top: 0; width: 100%; height: 39px;
    background: var(--header-bg);
  }
  .brand {
    position: absolute; left: 36px; top: 8px;
    font-size: 16px; font-weight: 700; letter-spacing: 0.2px; color: var(--ink);
  }
  .period-tabs { position: absolute; left: 140px; top: 0; height: 39px; display: flex; }
  .period-tab {
    height: 39px; line-height: 39px; font-size: 9px; color: var(--ink-soft);
    padding: 0 10px;
  }
  .period-tab.active { background: var(--tab-active); width: 41px; text-align: center; padding: 0; }
  .period-tab:nth-child(2) { padding-left: 11px; padding-right: 13px; }
  .main-nav {
    position: absolute; right: 37px; top: 0; height: 39px;
    display: flex; align-items: center; gap: 17px;
    font-size: 9px; color: var(--ink-soft);
  }
  .main-nav span { display: flex; align-items: center; gap: 3px; }
  .main-nav svg { width: 9px; height: 9px; fill: var(--ink); }

  .filter-bar {
    position: absolute; left: 0; top: 39px; width: 100%; height: 34px;
    background: var(--accent);
  }
  .filter-label {
    position: absolute; top: 11px; font-size: 9px; color: #fff;
  }
  .threshold {
    position: absolute; top: 9px; height: 17px; width: 124px;
    background: #fff; border-radius: 2px; display: flex; font-size: 7.5px;
  }
  .threshold .name {
    width: 46px; border-right: 1px solid #dde3e8; color: var(--accent);
    line-height: 17px; padding-left: 5px;
  }
  .threshold .value { line-height: 17px; padding-left: 5px; color: #5b6475; }

  .export {
    position: absolute; left: 36px; top: 87px;
    display: flex; align-items: center; gap: 3px;
    font-size: 9.5px; color: var(--ink);
  }
  .export svg { width: 8px; height: 8px; }

  .data-table { position: absolute; left: 36px; top: 112px; width: 507px; }
  .table-head, .table-row { display: grid; }
  .model-grid { grid-template-columns: 44px 65px 87px 81px 41px 39px 50px 46px 54px; }
  .factor-grid { grid-template-columns: 44px 65px 107px 55px 45px 45px 45px 47px 54px; }
  .table-head {
    height: 38px; box-shadow: 0 1px 2px rgba(40,50,70,0.08);
  }
  .table-head div {
    background: var(--head-cell); font-size: 8.5px; color: var(--ink-soft);
    display: flex; align-items: center; padding-left: 7px;
    border-right: 1px solid var(--rule);
  }
  .table-head div:last-child { border-right: none; }
  .table-head div.key { background: var(--head-cell-key); }
  .sort-caret { font-size: 4px; margin-left: 2px; }
  .table-row {
    height: 34.5px; margin-top: 5.5px; background: var(--row-bg);
    box-shadow: 0 0 0 1px rgba(200,205,212,0.5), 0 2px 3px rgba(40,50,70,0.06);
  }
  .table-row div {
    font-size: 7px; line-height: 9px; color: var(--ink-soft);
    display: flex; align-items: center; padding-left: 7px;
  }
  .table-row div.num { padding-left: 5px; }
  .table-head + .table-row { margin-top: 6px; }

  .site-footer {
    position: absolute; left: 0; width: 100%; text-align: center;
    font-size: 7.5px; color: var(--ink-soft);
  }
</style>
</head>
<body>

<!-- Models overview -->
<section class="screen screen-one">
  <header class="topbar">
    <div class="brand">Pellworth</div>
    <nav class="period-tabs"><span class="period-tab active">250D</span><span class="period-tab">83D</span><span class="period-tab">42D</span></nav>
    <nav class="main-nav">
      <span><svg viewBox="0 0 10 10"><path d="M5 1 0.5 5h1.3v4h2.4V6.5h1.6V9h2.4V5h1.3z"/></svg>Models</span>
      <span><svg viewBox="0 0 10 10"><path d="M4.4 0h1.2v10H4.4zM0 4.4h10v1.2H0zM1.2 2l.8-.8 6.8 6.8-.8.8zM8 1.2l.8.8L2 8.8 1.2 8z"/></svg>Sensitivities</span>
      <span><svg viewBox="0 0 10 10"><path d="M5 .3 6.4 3.4l3.3.3-2.5 2.2.8 3.3L5 7.5 2 9.2l.8-3.3L.3 3.7l3.3-.3z"/></svg>Favourites</span>
    </nav>
  </header>
  <div class="filter-bar">
    <span class="filter-label" style="left:36px">Quality</span>
    <div class="threshold" style="left:71px"><span class="name">Threshold:</span><span class="value">-10</span></div>
    <span class="filter-label" style="left:203px">Abs. stat</span>
    <div class="threshold" style="left:242px"><span class="name">Threshold:</span><span class="value">-10</span></div>
  </div>
  <div class="export"><svg viewBox="0 0 10 10"><rect width="10" height="10" rx="2" fill="#2f3a4f"/><path d="M3 7.5V5.2c0-1 .8-1.7 1.8-1.7H6V2.3L8 4.3 6 6.3V5H4.8c-.3 0-.5.2-.5.5v2z" fill="#fff"/></svg>Export</div>
  <div class="data-table">
    <div class="table-head model-grid"><div class="key">ID<span class="sort-caret">▼</span></div><div class="key">Sector</div><div class="key">Time</div><div>Quality</div><div>Stat 1</div><div>Stat 2</div><div>Stat 3</div><div>Stat 4</div><div>Stat 5</div></div>
    <div class="table-row model-grid"><div>Model 1</div><div>Materials</div><div>2019-07-03<br>12:15:00:00</div><div>30.2288</div><div>2.0125</div><div class="num">23.305</div><div class="num">-0.14587</div><div class="num">22.3254</div><div class="num">0.32548</div></div>
    <div class="table-row model-grid"><div>Model 2</div><div>Industrials</div><div>2019-07-03<br>12:15:00:00</div><div>30.2288</div><div>2.0125</div><div class="num">23.305</div><div class="num">-0.14587</div><div class="num">22.3254</div><div class="num">0.32548</div></div>
    <div class="table-row model-grid"><div>Model 3</div><div>Consumer<br>Discretionary</div><div>2019-07-03<br>12:15:00:00</div><div>30.2288</div><div>2.0125</div><div class="num">23.305</div><div class="num">-0.14587</div><div class="num">22.3254</div><div class="num">0.32548</div></div>
    <div class="table-row model-grid"><div>Model 4</div><div>Information<br>Technology</div><div>2019-07-03<br>12:15:00:00</div><div>30.2288</div><div>2.0125</div><div class="num">23.305</div><div class="num">-0.14587</div><div class="num">22.3254</div><div class="num">0.32548</div></div>
    <div class="table-row model-grid"><div>Model 5</div><div>Information<br>Technology</div><div>2019-07-03<br>12:15:00:00</div><div>30.2288</div><div>2.0125</div><div class="num">23.305</div><div class="num">-0.14587</div><div class="num">22.3254</div><div class="num">0.32548</div></div>
  </div>
  <footer class="site-footer" style="top:372px">© 2019 All rights reserved. Privacy Policy</footer>
</section>

<!-- Filtered models -->
<section class="screen screen-two">
  <header class="topbar">
    <div class="brand">Pellworth</div>
    <nav class="period-tabs"><span class="period-tab active">250D</span><span class="period-tab">83D</span><span class="period-tab">42D</span></nav>
    <nav class="main-nav">
      <span><svg viewBox="0 0 10 10"><path d="M5 1 0.5 5h1.3v4h2.4V6.5h1.6V9h2.4V5h1.3z"/></svg>Models</span>
      <span><svg viewBox="0 0 10 10"><path d="M4.4 0h1.2v10H4.4zM0 4.4h10v1.2H0zM1.2 2l.8-.8 6.8 6.8-.8.8zM8 1.2l.8.8L2 8.8 1.2 8z"/></svg>Sensitivities</span>
      <span><svg viewBox="0 0 10 10"><path d="M5 .3 6.4 3.4l3.3.3-2.5 2.2.8 3.3L5 7.5 2 9.2l.8-3.3L.3 3.7l3.3-.3z"/></svg>Favourites</span>
    </nav>
  </header>
  <div class="filter-bar">
    <span class="filter-label" style="left:36px">Quality</span>
    <div class="threshold" style="left:71px"><span class="name">Threshold:</span><span class="value">-10</span></div>
    <span class="filter-label" style="left:203px">Abs. stat</span>
    <div class="threshold" style="left:242px"><span class="name">Threshold:</span><span class="value">-10</span></div>
  </div>
  <div class="export"><svg viewBox="0 0 10 10"><rect width="10" height="10" rx="2" fill="#2f3a4f"/><path d="M3 7.5V5.2c0-1 .8-1.7 1.8-1.7H6V2.3L8 4.3 6 6.3V5H4.8c-.3 0-.5.2-.5.5v2z" fill="#fff"/></svg>Export</div>
  <div class="data-table">
    <div class="table-head model-grid"><div>ID<span class="sort-caret">▼</span></div><div>Sector</div><div>Time</div><div>Quality</div><div>Stat 1</div><div>Stat 2</div><div>Stat 3</div><div>Stat 4</div><div>Stat 5</div></div>
    <div class="table-row model-grid"><div>Model 1</div><div>Materials</div><div>2019-07-03<br>12:15:00:00</div><div>30.2288</div><div>2.0125</div><div class="num">23.305</div><div class="num">-0.14587</div><div class="num">22.3254</div><div class="num">0.32548</div></div>
    <div class="table-row model-grid"><div>Model 2</div><div>Industrials</div><div>2019-07-03<br>12:15:00:00</div><div>30.2288</div><div>2.0125</div><div class="num">23.305</div><div class="num">-0.14587</div><div class="num">22.3254</div><div class="num">0.32548</div></div>
  </div>
  <footer class="site-footer" style="top:256px">© 2019 All rights reserved. Privacy Policy</footer>
</section>

<!-- Factor sensitivities -->
<section class="screen screen-three">
  <header class="topbar">
    <div class="brand">Pellworth</div>
    <nav class="period-tabs"><span class="period-tab active">250D</span><span class="period-tab">83D</span><span class="period-tab">42D</span></nav>
    <nav class="main-nav">
      <span><svg viewBox="0 0 10 10"><path d="M5 1 0.5 5h1.3v4h2.4V6.5h1.6V9h2.4V5h1.3z"/></svg>Models</span>
      <span><svg viewBox="0 0 10 10"><path d="M4.4 0h1.2v10H4.4zM0 4.4h10v1.2H0zM1.2 2l.8-.8 6.8 6.8-.8.8zM8 1.2l.8.8L2 8.8 1.2 8z"/></svg>Sensitivities</span>
      <span><svg viewBox="0 0 10 10"><path d="M5 .3 6.4 3.4l3.3.3-2.5 2.2.8 3.3L5 7.5 2 9.2l.8-3.3L.3 3.7l3.3-.3z"/></svg>Favourites</span>
    </nav>
  </header>
  <div class="filter-bar">
    <span class="filter-label" style="left:36px">Stat 1</span>
    <div class="threshold" style="left:62px"><span class="name">Threshold:</span><span class="value">-10</span></div>
    <span class="filter-label" style="left:195px">Stat 2</span>
    <div class="threshold" style="left:221px"><span class="name">Threshold:</span><span class="value">-10</span></div>
    <span class="filter-label" style="left:358px">Stat 3</span>
    <div class="threshold" style="left:384px"><span class="name">Threshold:</span><span class="value">-10</span></div>
  </div>
  <div class="export"><svg viewBox="0 0 10 10"><rect width="10" height="10" rx="2" fill="#2f3a4f"/><path d="M3 7.5V5.2c0-1 .8-1.7 1.8-1.7H6V2.3L8 4.3 6 6.3V5H4.8c-.3 0-.5.2-.5.5v2z" fill="#fff"/></svg>Export</div>
  <div class="data-table">
    <div class="table-head factor-grid"><div class="key">Factor</div><div class="key">ID<span class="sort-caret">▼</span></div><div class="key">Sector</div><div>Stat 1</div><div>Stat 2</div><div>Stat 3</div><div>Stat 4</div><div>Stat 5</div><div>Stat 6</div></div>
    <div class="table-row factor-grid"><div>Factor 1</div><div>Model 1</div><div>Materials</div><div>-1.04</div><div class="num">0.3</div><div class="num">-3.1</div><div>0.7</div><div class="num">30.2</div><div>0.9</div></div>
    <div class="table-row factor-grid"><div>Factor 2</div><div>Model 2</div><div>Materials</div><div>-1.04</div><div class="num">0.3</div><div class="num">-3.1</div><div>0.7</div><div class="num">30.2</div><div>0.9</div></div>
    <div class="table-row factor-grid"><div>Factor 3</div><div>Model 3</div><div>Materials</div><div>-1.04</div><div class="num">0.3</div><div class="num">-3.1</div><div>0.7</div><div class="num">30.2</div><div>0.9</div></div>
    <div class="table-row factor-grid"><div>Factor 4</div><div>Model 4</div><div>Industrial</div><div>-1.04</div><div class="num">0.3</div><div class="num">-3.1</div><div>0.7</div><div class="num">30.2</div><div>0.9</div></div>
    <div class="table-row factor-grid"><div>Factor 5</div><div>Model 5</div><div>Industrial</div><div>-1.04</div><div class="num">0.3</div><div class="num">-3.1</div><div>0.7</div><div class="num">30.2</div><div>0.9</div></div>
  </div>
  <footer class="site-footer" style="top:372px">© 2019 All rights reserved. Privacy Policy</footer>
</section>

</body>
</html>
```